Machinery Harbor Corp - Business Card Design

Need a new modern designed business card that is different and stands out to represent my equipment financing company. Machinery Harbor Corp finances all types of equipment and all types of industries. We like to do equipment financing a different way by putting customers first and want our card to represent that different approach to business. I want a card that some remembers when they receive it so it sticks in their mind and makes that wow impression.

Card should have a black background so the logo stands out. It can be horizontial or vertical or a combination of both.

Front of card information is below that shows the information that would go on my card. That is where I want a different look or design to stand out. The front could be split black/orange colour so the logo could pop on black side and information on orange side with different lettering. Just outside the box thinking on the front of the card. Open to any type of design.

Back of card is below which i I like unless you have a different spin to provide or a different idea that would make the card better as I am open to anything that looks great.

Target Market(s)

Machinery Harbor Corp deals with business owners in all industries.

Industry/Entity Type

Business

Contact Information for Business Card

Colors

Designer to choose colors to be used in the design.

Requirements
Must have
• Modern
• Different
• Stand Out
• Makes an Impression

```html
<!DOCTYPE html>
<html lang="en">
<head>
<meta charset="utf-8">
<title>Machinery Harbor Corp – Business Card</title>
<link rel="stylesheet" href="https://fonts.googleapis.com/css2?family=Lato:wght@400;700&display=swap">
<style>
  :root {
    --stage: #2a2a2a;
    --card: #050505;
    --orange: #f07a1e;
    --white: #ffffff;
    --grey: #bdbdbd;
  }
  * { margin: 0; padding: 0; box-sizing: border-box; }
  html, body {
    width: 1200px;
    height: 800px;
    overflow: hidden;
    background: var(--stage);
    font-family: "Lato", Arial, sans-serif;
  }
  .stage {
    width: 1200px;
    height: 800px;
    display: flex;
    align-items: center;
    justify-content: center;
    gap: 60px;
  }
  .card {
    width: 460px;
    height: 460px;
    background: var(--card);
    border-radius: 32px;
    box-shadow: 0 14px 30px rgba(0, 0, 0, 0.55);
    position: relative;
  }
  .card-logo {
    display: flex;
    align-items: center;
    justify-content: center;
  }
  .brand-name {
    display: flex;
    align-items: center;
    gap: 14px;
    color: var(--orange);
    font-weight: 400;
    text-transform: uppercase;
    letter-spacing: 0.12em;
  }
  .brand-mark {
    width: 16px;
    height: 16px;
    border-radius: 50%;
    background: var(--orange);
    flex: none;
  }
  .card-logo .brand-name { font-size: 27px; line-height: 1.2; }
  .card-logo .brand-text { display: block; text-align: left; }
  .card-info {
    padding: 70px 56px 60px;
    display: flex;
    flex-direction: column;
    align-items: flex-end;
    text-align: right;
  }
  .card-info .brand-name { font-size: 22px; }
  .person { margin-top: 40px; }
  .person-name {
    color: var(--white);
    font-weight: 700;
    font-size: 24px;
    letter-spacing: 0.02em;
  }
  .person-title {
    color: var(--white);
    font-size: 16px;
    letter-spacing: 0.06em;
    margin-top: 2px;
  }
  .contact {
    margin-top: 44px;
    font-size: 16px;
    line-height: 1.7;
    color: var(--grey);
  }
  .contact .web { color: var(--orange); letter-spacing: 0.03em; }
</style>
</head>
<body>
  <main class="stage">
    <section class="card card-logo" aria-label="Card back">
      <div class="brand-name">
        <span class="brand-mark"></span>
        <span class="brand-text">Machinery<br>Harbor Corp</span>
      </div>
    </section>

    <section class="card card-info" aria-label="Card front">
      <div class="brand-name">
        <span class="brand-mark"></span>
        <span class="brand-text">Machinery Harbor Corp</span>
      </div>
      <div class="person">
        <p class="person-name">OWEN TARRANT</p>
        <p class="person-title">PRESIDENT</p>
      </div>
      <div class="contact">
        <p class="phone">555.014.2290</p>
        <p class="email">owen@machineryharborcorp.ca</p>
        <p class="web">www.machineryharborcorp.ca</p>
      </div>
    </section>
  </main>
</body>
</html>
```